Flat Belly Design Graphics for Social

I want to create 9 social media graphics (new Instagram size 4:5 (1080 x 1350 pixels) focusing on our Flat Belly Graphics, using the pics attached. Use the attached pics, NO RANDOM STOCK PHOTOGRAPHY. For the color scheme of the graphics, the color palette is attached. YOU MUST POST ALL 9 GRAPHICS IN ONE ENTRY.
Using the 3 titles below, create one set of graphics. 1) with all text, then for the others, use the pictures as detailed below in IMPORTANT:
1. Ten-Week Bright Morning Reboot
2. The Quick Garden Kitchen Menu Guide
3. Studio Habits for Lasting Energy Past Midlife - Zero Gym Needed
IMPORTANT:
Only use RK Pic 1 and RK Pic 2 with the title, Ten-Week Bright Morning Reboot
Only use meal plan1 and meal plan2 pics with the title, Quick Garden Kitchen Menu Guide
Only use studio habits 1 and studio habits 2 pics with the title, Studio Habits for Lasting Energy Past Midlife - Zero Gym Needed
women over 40

```html
<!DOCTYPE html>
<html lang="en">
<head>
<meta charset="utf-8">
<title>Bright Morning Reboot – Social Graphics Set</title>
<link href="https://fonts.googleapis.com/css2?family=Anton&family=Passion+One:wght@700&family=Montserrat:wght@800&display=swap" rel="stylesheet">
<style>
:root{
  --blush:#f8e1e5;
  --blush-light:#fcEEf0;
  --rose:#d9869c;
  --rose-mid:#e8a9b8;
  --forest:#1e4a44;
  --forest-dark:#143531;
  --white:#ffffff;
  --teal:#5cc3d4;
}
*{margin:0;padding:0;box-sizing:border-box}
html,body{width:1200px;height:1187px;overflow:hidden;background:var(--white)}
.board{
  width:1200px;height:1187px;padding:5px;
  display:grid;grid-template-columns:repeat(5,234px);grid-template-rows:repeat(4,290px);
  column-gap:5.5px;row-gap:5px;
}
.tile{position:relative;overflow:hidden;background:radial-gradient(ellipse at 40% 35%,var(--blush-light),var(--blush) 70%)}
.deco{position:absolute;inset:0;width:234px;height:290px}
.title{position:absolute;left:0;right:0;text-align:center;font-family:"Anton",sans-serif;text-transform:uppercase;line-height:.92;z-index:3}
.title.slant{transform:skewX(-9deg)}
.ln{display:block;text-shadow:1px 2px 2px rgba(20,53,49,.25)}
.green{color:var(--forest)}
.pink{color:var(--rose)}
.rounded{font-family:"Passion One",sans-serif;text-transform:none}
.wide{font-family:"Montserrat",sans-serif}
.photo{position:absolute;z-index:2}
.photo.person{background:linear-gradient(180deg,#c9a89a 0%,#f4f1ef 35%,#f4f1ef 60%,#1c1c1c 80%);border-radius:60px 60px 0 0}
.photo.pair{background:linear-gradient(180deg,#d8c3b8,#eac0b9 50%,#a9c9dc);border-radius:40px}
.photo.food{background:linear-gradient(135deg,#e7b39a,#8fa870 40%,#5a3d2a 70%,#c64a3a)}
.photo.frame{background:linear-gradient(135deg,#d94a3a,#7aa857 30%,#4a3428 50%,#f0b940 80%,#e56a4f)}
.dashes{position:absolute;left:40px;right:40px;height:4px;z-index:3;display:flex;gap:8px}
.dashes i{display:block;height:4px;background:var(--forest);border-radius:2px}
.menu-labels{position:absolute;left:184px;top:120px;width:46px;font-family:"Montserrat",sans-serif;font-weight:800;font-size:7px;color:var(--forest);z-index:3}
.menu-labels p{margin-bottom:26px;border-bottom:1px solid var(--rose-mid);padding-bottom:14px}
</style>
</head>
<body>
<svg width="0" height="0" style="position:absolute">
  <defs>
    <symbol id="deco-wave" viewBox="0 0 234 290">
      <path d="M0 70 Q90 40 234 110 L234 130 Q100 70 0 95Z" fill="#fff" opacity=".35"/>
      <path d="M95 0 Q55 8 30 30 Q65 12 110 4Z" fill="var(--forest)"/>
      <path d="M234 190 Q190 240 150 290 L234 290Z" fill="var(--rose-mid)" opacity=".7"/>
      <path d="M120 290 Q165 265 205 245 Q185 272 175 290Z" fill="var(--forest)"/>
    </symbol>
    <symbol id="deco-slash" viewBox="0 0 234 290">
      <path d="M150 18 L162 4 L172 4 L160 18Z M172 18 L184 4 L190 4 L178 18Z" fill="var(--forest)"/>
      <path d="M50 290 L62 276 L72 276 L60 290Z M72 290 L84 276 L92 276 L80 290Z" fill="var(--forest)"/>
      <path d="M0 165 Q28 170 26 205 Q22 240 0 250Z" fill="var(--forest)"/>
      <path d="M234 40 Q218 70 222 110 L234 115Z" fill="var(--forest)"/>
    </symbol>
  </defs>
</svg>

<main class="board">
  <!-- Row 1: Ten-Week Bright Morning Reboot -->
  <section class="tile">
    <svg class="deco"><use href="#deco-wave"/></svg>
    <div class="title slant" style="top:62px">
      <span class="ln green" style="font-size:36px">Ten-Week</span>
      <span class="ln pink" style="font-size:36px">Bright</span>
      <span class="ln pink" style="font-size:34px">Morning</span>
      <span class="ln green" style="font-size:40px">Reboot</span>
    </div>
    <div class="dashes" style="top:234px"><i style="width:36px"></i><i style="width:24px"></i><i style="width:8px"></i><i style="width:54px"></i></div>
  </section>

  <section class="tile">
    <svg class="deco"><use href="#deco-wave"/></svg>
    <div class="title slant" style="top:22px">
      <span class="ln green" style="font-size:34px">Ten-Week</span>
      <span class="ln pink" style="font-size:22px">Bright Morning</span>
      <span class="ln green" style="font-size:34px">Reboot</span>
    </div>
    <div class="photo person" role="img" aria-label="Smiling woman in cropped white sweater pointing down" style="left:52px;top:115px;width:130px;height:175px"></div>
  </section>

  <section class="tile">
    <svg class="deco"><use href="#deco-wave"/></svg>
    <div class="title slant" style="top:58px;right:90px">
      <span class="ln green" style="font-size:34px">Ten-Week</span>
      <span class="ln pink" style="font-size:34px">Bright</span>
      <span class="ln pink" style="font-size:30px">Morning</span>
      <span class="ln green" style="font-size:36px">Reboot</span>
    </div>
    <div class="photo person" role="img" aria-label="Smiling woman in cropped white sweater" style="left:118px;top:95px;width:116px;height:195px"></div>
  </section>

  <section class="tile">
    <svg class="deco"><use href="#deco-wave"/></svg>
    <div class="photo person" role="img" aria-label="Smiling woman in cropped white sweater pointing down" style="left:62px;top:20px;width:110px;height:140px"></div>
    <div class="title slant" style="top:145px">
      <span class="ln green" style="font-size:30px">The Quick</span>
      <span class="ln pink" style="font-size:24px">Garden Kitchen</span>
      <span class="ln green" style="font-size:30px">Menu Guide</span>
    </div>
    <div class="dashes" style="top:278px;left:56px"><i style="width:24px"></i><i style="width:18px"></i><i style="width:6px"></i><i style="width:44px"></i></div>
  </section>

  <section class="tile">
    <svg class="deco"><use href="#deco-wave"/></svg>
    <div class="title slant" style="top:10px">
      <span class="ln green" style="font-size:28px">The Quick</span>
      <span class="ln pink" style="font-size:24px">Garden Kitchen</span>
      <span class="ln green" style="font-size:28px">Menu Guide</span>
    </div>
    <div class="dashes" style="top:138px;left:44px"><i style="width:36px"></i><i style="width:10px"></i><i style="width:50px"></i></div>
    <div class="photo person" role="img" aria-label="Smiling woman in cropped pink sweater pointing down" style="left:56px;top:130px;width:124px;height:160px"></div>
  </section>

  <!-- Row 2: Quick Garden Kitchen Menu Guide -->
  <section class="tile">
    <svg class="deco"><use href="#deco-slash"/></svg>
    <div class="title" style="top:48px">
      <span class="ln green" style="font-size:52px">The Quick</span>
      <span class="ln green" style="font-size:44px">Garden</span>
      <span class="ln pink" style="font-size:34px">Kitchen Menu</span>
      <span class="ln green" style="font-size:40px">Guide</span>
    </div>
    <div class="dashes" style="top:232px;left:40px"><i style="width:30px"></i><i style="width:44px"></i><i style="width:4px;margin-left:30px"></i><i style="width:4px"></i><i style="width:4px"></i></div>
  </section>

  <section class="tile">
    <svg class="deco"><use href="#deco-slash"/></svg>
    <div class="title" style="top:32px">
      <span class="ln green" style="font-size:28px">The Quick Garden</span>
      <span class="ln pink" style="font-size:18px">Kitchen Menu Guide</span>
    </div>
    <div class="photo food" role="img" aria-label="Table of chicken, fruit, vegetables and a written meal plan" style="left:28px;top:104px;width:180px;height:130px;border-radius:60px 80px 50px 70px;border:5px solid var(--rose-mid)"></div>
  </section>

  <section class="tile">
    <svg class="deco"><use href="#deco-slash"/></svg>
    <div class="title" style="top:28px">
      <span class="ln green" style="font-size:28px">The Quick</span>
      <span class="ln pink" style="font-size:30px">Garden Kitchen</span>
      <span class="ln green" style="font-size:32px">Menu Guide</span>
    </div>
    <div class="photo food" role="img" aria-label="Table of chicken, fruit, vegetables and a written meal plan" style="left:24px;top:124px;width:186px;height:108px"></div>
    <div class="dashes" style="top:242px;left:42px"><i style="width:26px"></i><i style="width:46px"></i><i style="width:4px;margin-left:30px"></i><i style="width:4px"></i><i style="width:4px"></i></div>
  </section>

  <section class="tile">
    <svg class="deco"><use href="#deco-slash"/></svg>
    <div class="title" style="top:30px">
      <span class="ln green" style="font-size:28px">The Quick Garden</span>
      <span class="ln pink" style="font-size:18px">Kitchen Menu Guide</span>
    </div>
    <div class="photo frame" role="img" aria-label="Fresh produce and salmon framing a notepad on wood" style="left:32px;top:108px;width:176px;height:120px;border:3px solid var(--forest)"></div>
    <div class="dashes" style="top:232px;left:60px"><i style="width:50px"></i><i style="width:40px"></i><i style="width:4px;margin-left:8px"></i><i style="width:4px"></i></div>
  </section>

  <section class="tile">
    <svg class="deco"><use href="#deco-slash"/></svg>
    <div class="title" style="top:26px">
      <span class="ln green" style="font-size:28px">The Quick</span>
      <span class="ln pink" style="font-size:28px">Garden Kitchen</span>
      <span class="ln green" style="font-size:28px">Menu Guide</span>
    </div>
    <div class="photo frame" role="img" aria-label="Fresh produce and salmon framing a notepad on wood" style="left:18px;top:130px;width:200px;height:132px;border-radius:20px;border:3px solid var(--forest)"></div>
  </section>

  <!-- Row 3: Studio Habits -->
  <section class="tile">
    <svg class="deco"><use href="#deco-wave"/></svg>
    <div class="title slant" style="top:68px">
      <span class="ln green" style="font-size:32px">Studio Habits</span>
      <span class="ln green" style="font-size:30px">for Lasting</span>
      <span class="ln green" style="font-size:30px">Energy</span>
      <span class="ln pink" style="font-size:34px">Past Midlife</span>
      <span class="ln green" style="font-size:15px;margin-top:6px">- Zero Gym Needed</span>
    </div>
  </section>

  <section class="tile">
    <svg class="deco"><use href="#deco-wave"/></svg>
    <div class="photo pair" role="img" aria-label="Two women sharing a whispered secret" style="left:120px;top:6px;width:110px;height:140px;opacity:.8"></div>
    <div class="title slant" style="top:68px">
      <span class="ln green" style="font-size:32px">Studio Habits</span>
      <span class="ln green" style="font-size:30px">for Lasting</span>
      <span class="ln green" style="font-size:30px">Energy</span>
      <span class="ln pink" style="font-size:34px">Past Midlife</span>
      <span class="ln green" style="font-size:15px;margin-top:6px">- Zero Gym Needed</span>
    </div>
  </section>

  <section class="tile">
    <svg class="deco"><use href="#deco-wave"/></svg>
    <div class="title slant" style="top:20px">
      <span class="ln green" style="font-size:21px">Studio Habits for Lasting</span>
      <span class="ln green" style="font-size:21px">Energy Past Midlife</span>
      <span class="ln green" style="font-size:12px;margin-top:2px">- Zero Gym Needed</span>
    </div>
    <svg class="deco" viewBox="0 0 234 290"><path d="M0 200 Q60 170 110 230 Q160 280 234 250 L234 290 L0 290Z" fill="var(--rose-mid)"/><path d="M0 215 Q40 195 70 240 Q30 230 0 260Z" fill="var(--forest)"/></svg>
    <div class="photo pair" role="img" aria-label="Two women sharing a whispered secret" style="left:50px;top:100px;width:140px;height:170px"></div>
  </section>

  <section class="tile">
    <svg class="deco"><use href="#deco-wave"/></svg>
    <div class="photo pair" role="img" aria-label="Two women sharing a whispered secret" style="left:100px;top:0;width:134px;height:180px;opacity:.8"></div>
    <div class="title slant" style="top:68px">
      <span class="ln green" style="font-size:32px">Studio Habits</span>
      <span class="ln green" style="font-size:30px">for Lasting</span>
      <span class="ln green" style="font-size:30px">Energy</span>
      <span class="ln pink" style="font-size:34px">Past Midlife</span>
      <span class="ln green" style="font-size:15px;margin-top:6px">- Zero Gym Needed</span>
    </div>
  </section>

  <section class="tile">
    <svg class="deco"><use href="#deco-wave"/></svg>
    <div class="title slant" style="top:26px">
      <span class="ln green" style="font-size:34px">Studio Habits</span>
      <span class="ln green" style="font-size:34px">for Energy</span>
      <span class="ln pink" style="font-size:36px">Past Midlife</span>
      <span class="ln green" style="font-size:15px;margin-top:4px">- Zero Gym Needed</span>
    </div>
    <div class="photo pair" role="img" aria-label="Two women sharing a whispered secret" style="left:18px;top:155px;width:196px;height:135px;border-radius:50px 50px 0 0"></div>
  </section>

  <!-- Row 4 -->
  <section class="tile">
    <svg class="deco" viewBox="0 0 234 290"><path d="M0 0 L234 0 L234 30 Q130 20 40 110 Q15 140 0 180Z" fill="var(--forest)"/><path d="M0 60 Q80 0 234 10 L234 0 L0 0Z" fill="var(--rose-mid)"/><path d="M234 200 Q190 250 150 290 L234 290Z" fill="var(--rose-mid)"/></svg>
    <div class="photo pair" role="img" aria-label="Two women sharing a whispered secret" style="left:40px;top:0;width:160px;height:95px;border-radius:0 0 40px 40px"></div>
    <div class="title slant" style="top:68px">
      <span class="ln green" style="font-size:32px">Studio Habits</span>
      <span class="ln green" style="font-size:30px">for Lasting</span>
      <span class="ln green" style="font-size:30px">Energy</span>
      <span class="ln pink" style="font-size:34px">Past Midlife</span>
      <span class="ln green" style="font-size:15px;margin-top:6px">- Zero Gym Needed</span>
    </div>
  </section>

  <section class="tile">
    <svg class="deco"><use href="#deco-wave"/></svg>
    <div class="title rounded" style="top:40px">
      <span class="ln green" style="font-size:33px">Studio Habits</span>
      <span class="ln green" style="font-size:33px">for Lasting</span>
      <span class="ln green" style="font-size:33px">Energy</span>
      <span class="ln pink slant" style="font-size:36px;font-family:'Anton',sans-serif;text-transform:uppercase">Past Midlife</span>
      <span class="ln green" style="font-size:33px">- Zero Gym</span>
      <span class="ln green" style="font-size:33px">Needed</span>
    </div>
  </section>

  <section class="tile">
    <svg class="deco"><use href="#deco-wave"/></svg>
    <div class="title slant" style="top:28px">
      <span class="ln green" style="font-size:28px">Studio Habits</span>
      <span class="ln green" style="font-size:16px">for Lasting Energy</span>
      <span class="ln pink" style="font-size:32px">Past Midlife</span>
    </div>
    <div class="photo" role="img" aria-label="Two women sharing a whispered secret on a teal backdrop" style="left:30px;top:110px;width:176px;height:120px;background:linear-gradient(135deg,var(--teal),#eac0b9 60%,#a9c9dc);border-radius:30px 20px 40px 20px;transform:skewX(-8deg)"></div>
    <div class="title slant" style="top:248px"><span class="ln green" style="font-size:15px">- Zero Gym Needed</span></div>
  </section>

  <section class="tile">
    <svg class="deco" viewBox="0 0 234 290"><path d="M160 0 Q200 20 234 0Z M180 0 Q215 30 234 60 L234 0Z" fill="var(--forest)"/><path d="M234 180 Q220 230 234 260Z" fill="var(--forest)"/></svg>
    <div class="title wide" style="top:20px;text-align:left;left:20px">
      <span class="ln green" style="font-size:20px;line-height:1.1">The Quick</span>
      <span class="ln pink" style="font-size:20px;line-height:1.1">Garden Kitchen</span>
      <span class="ln green" style="font-size:20px;line-height:1.1">Menu Guide</span>
    </div>
    <div class="photo food" role="img" aria-label="Table of chicken, fruit, vegetables and a written meal plan" style="left:20px;top:114px;width:152px;height:150px;border:3px solid var(--forest)"></div>
    <div class="menu-labels"><p>BREAKFAST</p><p>LUNCH</p><p>DINNER</p><p>SNACK</p></div>
  </section>

  <section class="tile">
    <svg class="deco"><use href="#deco-slash"/></svg>
    <div class="title" style="top:14px">
      <span class="ln green" style="font-size:36px">The Quick</span>
      <span class="ln green" style="font-size:30px">Garden</span>
      <span class="ln pink" style="font-size:26px">Kitchen Menu</span>
      <span class="ln green" style="font-size:30px">Guide</span>
    </div>
    <div class="photo frame" role="img" aria-label="Fresh produce and salmon framing a notepad" style="left:24px;top:138px;width:188px;height:132px;border:3px solid var(--forest)"></div>
  </section>
</main>
</body>
</html>
```